design a construction company business card

Design business card around our logo. Card must have all the typical info: name, title, address, phone, email, business name, etc. Somewhere on the card I would like to see our motto "Solid foundations... Lasting partnerships." Consider adding a splash of bright orange to the card to complement the blues and silvers/grays in the logo. We are open to metallic inks, textures, etc. We would like to see options on both light and dark backgrounds. The font in the logo is Euro Technic Extended Regular.

```html
<!DOCTYPE html>
<html lang="en">
<head>
<meta charset="utf-8">
<title>Halden Builders – Business Card</title>
<link href="https://fonts.googleapis.com/css2?family=Open+Sans:wght@400;600;700&display=swap" rel="stylesheet">
<style>
  :root {
    --stage: #e9eaee;
    --blue-deep: #2b3f9e;
    --blue-mid: #1f5fbf;
    --blue-bright: #1a78c9;
    --ink-blue: #2a4aa8;
    --gray: #8a8d93;
    --gray-line: #c9cbd0;
    --text: #3a3c40;
    --white: #ffffff;
  }
  * { box-sizing: border-box; margin: 0; padding: 0; }
  html, body {
    width: 1200px; height: 892px; overflow: hidden;
    background: var(--stage);
    font-family: "Open Sans", Arial, sans-serif;
  }
  .canvas { position: relative; width: 1200px; height: 892px; }

  .card {
    position: absolute; width: 525px; height: 300px;
    box-shadow: 0 10px 28px rgba(0,0,0,.18);
    overflow: hidden;
  }

  /* Back side */
  .card-back {
    left: 70px; top: 110px;
    background: radial-gradient(ellipse at 58% 45%, var(--blue-bright) 0%, var(--blue-mid) 40%, var(--blue-deep) 100%);
    color: var(--white);
  }
  .back-brand {
    position: absolute; left: 0; right: 0; top: 112px;
    text-align: center;
    font-size: 34px; font-weight: 600; letter-spacing: 4px;
  }
  .back-rule {
    position: absolute; left: 118px; width: 290px; top: 166px;
    height: 3px; background: var(--white);
  }
  .tagline {
    position: absolute; left: 0; right: 0; top: 178px;
    text-align: center; font-size: 14px; letter-spacing: .3px;
  }

  /* Front side */
  .card-front { left: 605px; top: 482px; background: var(--white); }
  .front-bands { position: absolute; inset: 0; }

  .front-brand {
    position: absolute; left: 28px; top: 128px; width: 210px;
    text-align: center;
  }
  .front-brand .brand-name {
    font-size: 30px; font-weight: 700; color: var(--ink-blue); letter-spacing: 2px;
  }
  .front-brand .brand-sub {
    margin-top: 2px; font-size: 11px; font-weight: 400;
    color: var(--gray); letter-spacing: 2.5px;
  }

  .divider {
    position: absolute; left: 238px; top: 92px; width: 1px; height: 100px;
    background: linear-gradient(var(--gray-line), transparent);
    transform: rotate(-18deg); transform-origin: top;
  }

  .contact { position: absolute; left: 282px; top: 74px; }
  .contact .person { font-size: 17px; font-weight: 700; color: var(--ink-blue); line-height: 1.1; }
  .contact .role { font-size: 11px; color: var(--gray); letter-spacing: .5px; margin-bottom: 7px; }
  .contact .address { font-size: 11.5px; color: var(--text); line-height: 1.35; margin-bottom: 6px; }
  .contact ul { list-style: none; }
  .contact li {
    display: flex; align-items: center; gap: 8px;
    font-size: 11.5px; color: var(--text); line-height: 1.6;
  }
  .contact li svg { width: 12px; height: 12px; flex: none; }
</style>
</head>
<body>
<main class="canvas">

  <section class="card card-back" aria-label="Card back">
    <div class="back-brand">HALDEN</div>
    <div class="back-rule"></div>
    <p class="tagline">Solid foundations... Lasting partnerships.</p>
  </section>

  <section class="card card-front" aria-label="Card front">
    <svg class="front-bands" viewBox="0 0 525 300" preserveAspectRatio="none" aria-hidden="true">
      <defs>
        <linearGradient id="band" x1="0" x2="1" y1="0" y2="0">
          <stop offset="0" stop-color="#2b3f9e"/>
          <stop offset="1" stop-color="#1a6fc8"/>
        </linearGradient>
      </defs>
      <polygon fill="url(#band)" points="0,0 525,0 525,0 525,0 490,70 245,70 225,40 0,40" transform="translate(0,-26)"/>
      <polygon fill="url(#band)" points="0,300 525,300 525,278 300,278 280,260 0,260" transform="translate(0,12)"/>
      <polygon fill="url(#band)" points="0,300 0,252 40,224 180,224 200,245 160,300"/>
    </svg>

    <div class="front-brand">
      <div class="brand-name">HALDEN</div>
      <div class="brand-sub">BUILDERS, INC.</div>
    </div>

    <div class="divider"></div>

    <div class="contact">
      <div class="person">MARK ELLISON</div>
      <div class="role">PRESIDENT</div>
      <div class="address">2170 Ridgeview Lane<br>Oak Hollow, NY 11420</div>
      <ul>
        <li>
          <svg viewBox="0 0 12 12"><path fill="#2a4aa8" d="M3 1l2 2-1 1.5c.6 1.3 1.4 2.1 2.6 2.6L8 6l2 2-1.2 1.8C5 9.6 2.3 7 2 3.2z"/></svg>
          555 0147 2290
        </li>
        <li>
          <svg viewBox="0 0 12 12"><rect x="1" y="3" width="10" height="7" rx="1" fill="#2a4aa8"/><path d="M1.5 3.5L6 7l4.5-3.5" stroke="#fff" fill="none"/></svg>
          mark@haldenbuilders.com
        </li>
        <li>
          <svg viewBox="0 0 12 12"><circle cx="6" cy="6" r="5" fill="#2a4aa8"/><path d="M1 6h10M6 1c-2 2.8-2 7.2 0 10M6 1c2 2.8 2 7.2 0 10" stroke="#fff" stroke-width=".7" fill="none"/></svg>
          www.haldenbuilders.com
        </li>
      </ul>
    </div>
  </section>

</main>
</body>
</html>
```